Business card for a Exhibition booth fabrication company

Hi. My company would like to change our corporate name card. We are an events and Exhibition stand builder company. We would like our corporate name card to resonate what we do. I need someone to create something unique that relates to the industry that I am in. The graphic designer should be creative to incorporate the elements of my industry and try to blend in well in the design of the card. Our aim is to ensure that we are unique and our card can look different from our competitors.
Updates

Target Market(s)

Marketing and events manager from all companies

Contact Information for Business Card

The business card should have the following details:
Name
Job Title
Email
Website

Colors

Designer to choose colors to be used in the design.

Requirements
Must have
• The card must be look something that is relevant to the service that I am providing. My website is: www.velmora-buildworks.com
• You can see my website to get more information on what service that I am doing
Nice to have
• On the back of my card, I would like to have a globe image with the incorporation of my company logo. This is to indicate that my services can be done in any part of the world.

```html
<!DOCTYPE html>
<html lang="en">
<head>
<meta charset="utf-8">
<title>Velmora Buildworks – Business Card</title>
<link href="https://fonts.googleapis.com/css2?family=Open+Sans:wght@400;600&family=Roboto+Condensed:wght@700&family=PT+Serif&display=swap" rel="stylesheet">
<style>
  :root {
    --page: #e9e7e4;
    --card: #ffffff;
    --red: #e21f26;
    --black: #161616;
    --ink: #3a3a3a;
    --grey: #5a5a5a;
    --map-light: #f1f1f1;
    --map-dark: #bdbdbd;
  }
  * { margin: 0; padding: 0; box-sizing: border-box; }
  html, body { width: 1200px; height: 1200px; overflow: hidden; background: var(--page); }
  .stage {
    width: 1200px; height: 1200px;
    display: flex; flex-direction: column; align-items: center; justify-content: center; gap: 50px;
  }
  .card {
    position: relative; width: 900px; height: 514px; background: var(--card);
    overflow: hidden; box-shadow: 0 6px 22px rgba(0,0,0,.18);
  }

  /* Back side */
  .back .world-map {
    position: absolute; left: 280px; top: 40px; width: 580px; height: 440px;
    border-radius: 50%;
    background: radial-gradient(ellipse at 45% 45%, var(--map-dark) 0%, #d2d2d2 45%, var(--map-light) 75%, transparent 100%);
    opacity: .8;
  }
  .back .brand {
    position: absolute; left: 0; right: 0; top: 230px;
    display: flex; align-items: center; justify-content: center; gap: 18px;
    font-family: "Open Sans", sans-serif; font-weight: 600; font-size: 40px;
    letter-spacing: 6px; color: var(--ink);
  }
  .brand .dot { width: 26px; height: 26px; border-radius: 50%; background: var(--red); flex: none; }

  /* Front side */
  .front .brand-small {
    position: absolute; left: 70px; top: 48px;
    display: flex; align-items: center; gap: 12px;
    font-family: "Open Sans", sans-serif; font-weight: 600; font-size: 20px;
    letter-spacing: 3px; color: var(--ink);
  }
  .brand-small .dot { width: 16px; height: 16px; border-radius: 50%; background: var(--red); }
  .person { position: absolute; left: 70px; top: 118px; }
  .person .name {
    font-family: "Roboto Condensed", sans-serif; font-weight: 700; font-size: 44px; line-height: 1;
  }
  .name .first { color: var(--red); }
  .name .last { color: var(--grey); }
  .person .title {
    font-family: "PT Serif", serif; font-size: 22px; color: var(--ink); margin-top: 6px;
  }
  .graphics { position: absolute; inset: 0; }
  .contacts {
    position: absolute; left: 40px; top: 238px;
    font-family: "Open Sans", sans-serif; font-size: 21px; color: #fff;
    display: flex; flex-direction: column; gap: 14px;
  }
  .contacts li { list-style: none; display: flex; align-items: center; gap: 14px; }
  .contacts svg { width: 22px; height: 22px; flex: none; }
</style>
</head>
<body>
<main class="stage">

  <section class="card back">
    <div class="world-map" role="img" aria-label="Soft grey world map showing global reach"></div>
    <div class="brand"><span class="dot"></span>VELMORA BUILDWORKS</div>
  </section>

  <section class="card front">
    <svg class="graphics" viewBox="0 0 900 514" aria-hidden="true">
      <polygon points="0,212 470,212 530,346 0,346" fill="var(--black)"/>
      <polygon points="0,362 560,362 590,396 0,396" fill="var(--black)"/>
      <polygon points="40,412 560,412 580,432 60,432" fill="var(--red)"/>
      <polygon points="90,444 880,444 900,478 110,478" fill="var(--red)"/>
      <polygon points="540,490 800,490 820,514 560,514" fill="var(--red)"/>
    </svg>

    <div class="brand-small"><span class="dot"></span>VELMORA BUILDWORKS</div>

    <div class="person">
      <div class="name"><span class="first">Daniel</span> <span class="last">Reyes</span></div>
      <div class="title">Director</div>
    </div>

    <ul class="contacts">
      <li>
        <svg viewBox="0 0 22 22"><rect width="22" height="22" rx="3" fill="var(--red)"/><rect x="4" y="6" width="14" height="10" fill="none" stroke="#fff" stroke-width="1.5"/><polyline points="4,6 11,12 18,6" fill="none" stroke="#fff" stroke-width="1.5"/></svg>
        username@velmora-buildworks.com
      </li>
      <li>
        <svg viewBox="0 0 22 22"><circle cx="11" cy="11" r="11" fill="var(--red)"/><circle cx="11" cy="11" r="7" fill="none" stroke="#fff" stroke-width="1.3"/><ellipse cx="11" cy="11" rx="3" ry="7" fill="none" stroke="#fff" stroke-width="1.3"/><line x1="4" y1="11" x2="18" y2="11" stroke="#fff" stroke-width="1.3"/></svg>
        www.velmora-buildworks.com
      </li>
    </ul>
  </section>

</main>
</body>
</html>
```